Counselling business needs a DL brochure design ready for print next week!

My business is called Quiet Harbour Counselling. My name is Megan Trelawny and I'm a qualified Psychotherapist based in Sydney, Australia.

I need a DL brochure to promote my business. I like the idea of possibly incorporating a leaf/leaves and/or the colour green in a sophisticated, understated way in the DL design. I have attached a leaf image for reference. I am looking for a simple, elegant design overall. Not too many fonts, something which is easy to read and captures people's interest.

I need a print ready design - something that my local instant printer can use easily. I need a print ready PDF and original files too for the printer. I am anticipating that the design will be A4 folded to DL as it needs to fit into standard dimension plastic DL stands at various locations.

My business is focussed upon helping people overcome difficulties such as grief or anxiety. I also work with people to help them plan their life adventures. My business is different from the average counselling business. For example, I give my clients a beautiful thick stock postcard at the end of every session with takeaway learnings and insights which they've uncovered. That way, they can reflect upon those discoveries and capitalise upon them.

I have an office in a local wellness centre. The brochure will be showcased at the centre and in local medical centres and shops. The aim is that new prospects will pick up the brochure and be prompted to call me for a counselling appointment.

I have attached copy for my DL brochure and a competitor's DL for reference. I'm not seeking to emulate the competitor, but I thought that it could be a useful reference - the competitor DL is clear and easy to read. I need my photo to be included in the brochure, adjacent to the information about my background. I have attached a reference photo for use as a positional - a full size image will need to be dropped in as part of this job by the winning designer.

I do not have a company logo at the moment, but I need my business name and contact details repeated several times in the DL.
Updates

Hello. Thank you for your designs. I am so pleased to have received them. I will be in touch in the next 24 hours. Best, Megan

Industry/Entity Type

Business

```html
<!DOCTYPE html>
<html lang="en">
<head>
<meta charset="utf-8">
<title>Quiet Harbour Counselling – DL Brochure</title>
<link href="https://fonts.googleapis.com/css2?family=Cabin:ital,wght@0,500;0,600;0,700;1,500;1,600;1,700&display=swap" rel="stylesheet">
<style>
  :root {
    --green: #80b342;
    --charcoal: #58585a;
    --ink: #454547;
    --paper: #ffffff;
    --backdrop: #e9e7e3;
    --rule: #d9d9d9;
  }
  * { box-sizing: border-box; margin: 0; padding: 0; }
  html, body { width: 1200px; height: 861px; overflow: hidden; }
  body {
    background: var(--backdrop);
    font-family: "Cabin", Arial, sans-serif;
    position: relative;
  }
  .brochure {
    position: absolute; left: 44px; top: 38px;
    width: 1112px; height: 785px;
    background: var(--paper);
    box-shadow: 0 4px 14px rgba(0,0,0,.18);
  }
  .fold { position: absolute; top: 0; bottom: 0; width: 1px; background: var(--rule); }
  .fold--one { left: 370px; }
  .fold--two { left: 742px; }

  /* Panel one */
  .questions {
    position: absolute; left: 8px; top: 7px; width: 353px; height: 546px;
    background: var(--charcoal);
    color: #fff; text-align: center;
    font-style: italic; font-weight: 600; font-size: 17px; line-height: 1.32;
    padding-top: 46px;
  }
  .questions p { margin-bottom: 16px; }
  .photo-joy {
    position: absolute; left: 8px; top: 553px; width: 353px; height: 224px;
    background: linear-gradient(160deg, #9cbf5e 0%, #6f9a3c 55%, #4e7b2e 100%);
  }

  /* Panel two */
  .wordmark {
    position: absolute; color: var(--green);
    font-weight: 700; text-transform: uppercase; line-height: 1.05;
  }
  .wordmark--small { left: 398px; top: 54px; font-size: 21px; }
  .wordmark--large { left: 887px; top: 48px; font-size: 23px; }
  .mark-dot {
    position: absolute; left: 795px; top: 29px; width: 78px; height: 78px;
    border-radius: 50%; background: var(--green);
  }
  .photo-family {
    position: absolute; left: 379px; top: 143px; width: 723px; height: 412px;
    background: linear-gradient(180deg, #4d8fd0 0%, #8ec0ea 45%, #cfe3ec 62%, #a8c25a 72%, #7fa23a 100%);
  }
  .headline {
    position: absolute; left: 400px; top: 315px; width: 320px;
    text-align: center; color: var(--ink);
    font-style: italic; font-weight: 600; font-size: 22px; line-height: 1.4;
  }
  .band {
    position: absolute; background: var(--green); color: #fff;
    font-style: italic; font-weight: 600; text-align: center;
    display: flex; align-items: center; justify-content: center;
  }
  .band--need { left: 412px; top: 406px; width: 292px; height: 45px; font-size: 24px; }
  .band--hand { left: 425px; top: 456px; width: 266px; height: 45px; font-size: 26px; }
  .contact {
    position: absolute; left: 380px; top: 625px; width: 352px;
    text-align: center; color: var(--ink); font-style: italic; font-weight: 600;
  }
  .contact__phone { font-size: 23px; letter-spacing: 1.5px; margin-bottom: 9px; }
  .contact__line { font-size: 16px; margin-bottom: 9px; }

  /* Panel three */
  .band--overcome { left: 782px; top: 573px; width: 292px; height: 46px; font-size: 21px; }
  .band--fresh { left: 793px; top: 622px; width: 270px; height: 45px; font-size: 26px; }
  .phone-bar {
    position: absolute; left: 781px; top: 691px; width: 294px; height: 37px;
    background: var(--charcoal); color: #fff;
    display: flex; align-items: center; justify-content: center; gap: 14px;
    font-style: italic; font-weight: 600; font-size: 22px; letter-spacing: 2px;
  }
  .site {
    position: absolute; left: 762px; top: 741px; width: 330px; text-align: center;
    color: var(--green); font-style: italic; font-weight: 700; font-size: 17px;
  }
</style>
</head>
<body>
  <main class="brochure">
    <div class="fold fold--one"></div>
    <div class="fold fold--two"></div>

    <section class="questions">
      <p>DO YOU NEED<br>A POSITIVE CHANGE?</p>
      <p>DO YOU WISH You felt<br>more joyful and fulfilled?</p>
      <p>You felt less stressed<br>or overwhelmed?</p>
      <p>You coped better with<br>life’s challenges?</p>
      <p>You could break unhelpful habits?</p>
      <p>DO YOU IMAGINE Your<br>relationships being closer?</p>
      <p>Your life being well balanced?</p>
      <p>Your goals being within reach?</p>
      <p>Your life being more adventurous?</p>
    </section>
    <div class="photo-joy" role="img" aria-label="Photo of a woman with open arms enjoying fresh air by a green lakeside"></div>

    <div class="wordmark wordmark--small">Quiet Harbour<br>Counselling</div>

    <div class="photo-family" role="img" aria-label="Photo of a happy family in a sunny green meadow under a blue sky"></div>
    <p class="headline">The Power To Create New Possibilities Is Within You.</p>
    <div class="band band--need">You Might Just Need</div>
    <div class="band band--hand">A Helping Hand</div>

    <div class="contact">
      <p class="contact__phone">0412 555 019</p>
      <p class="contact__line">name@quietharbourcounselling.com</p>
      <p class="contact__line">www.quietharbourcounselling.com</p>
    </div>

    <div class="mark-dot"></div>
    <div class="wordmark wordmark--large">Quiet Harbour<br>Counselling</div>

    <div class="band band--overcome">Overcome Difficulties and</div>
    <div class="band band--fresh">Make A Fresh Start</div>
    <div class="phone-bar">
      <svg width="18" height="20" viewBox="0 0 24 24" aria-hidden="true"><path fill="#fff" d="M6.6 10.8a15.1 15.1 0 0 0 6.6 6.6l2.2-2.2c.3-.3.7-.4 1-.2 1.1.4 2.3.6 3.6.6.6 0 1 .4 1 1V20c0 .6-.4 1-1 1A17 17 0 0 1 3 4c0-.6.4-1 1-1h3.5c.6 0 1 .4 1 1 0 1.3.2 2.5.6 3.6.1.3 0 .7-.2 1z"/></svg>
      <span>0412 555 019</span>
    </div>
    <p class="site">www.quietharbourcounselling.com</p>
  </main>
</body>
</html>
```